Redesign business cards

We have a new logo and I am not that happy with the layout of our existing card and looking for a change. Font is a bit small and the green can be hard to read. Logo may need a tidy up as the copy I have is not that hi-res too so require you to produce a hi-res version of the logo for us too. There will be three individual business cards to produce with just the names and phone numbers being different. Address will change too, but use what you see on the card for now.

Industry/Entity Type

Business

Requirements
Nice to have
• You could consider a redesign to the new logo, just not too radical. We like the blue and green hexagons as we feel that they are representative of oil industry that we are in.

```html
<!DOCTYPE html>
<html lang="en">
<head>
<meta charset="utf-8">
<title>Verdane Oil Services – Business Cards</title>
<link href="https://fonts.googleapis.com/css2?family=Open+Sans:wght@400;600;700&display=swap" rel="stylesheet">
<style>
  :root {
    --backdrop: #e6e8ec;
    --card-white: #f4f4f4;
    --brand-green: #7cb53a;
    --brand-orange: #f9b042;
    --swoosh-grey: #6d6f73;
    --ink-white: #ffffff;
    --card-shadow: rgba(40, 46, 60, 0.18);
  }
  * { box-sizing: border-box; margin: 0; padding: 0; }
  html, body {
    width: 1200px;
    height: 866px;
    overflow: hidden;
    background: var(--backdrop);
    font-family: "Open Sans", Arial, sans-serif;
  }
  .canvas {
    position: relative;
    width: 1200px;
    height: 866px;
  }
  .card {
    position: absolute;
    width: 600px;
    height: 340px;
    background: radial-gradient(ellipse at 40% 45%, #ffffff 0%, var(--card-white) 70%, #e9e9e9 100%);
    box-shadow: 0 10px 28px var(--card-shadow);
    overflow: hidden;
  }
  .card--front { left: 60px; top: 60px; }
  .card--back  { left: 540px; top: 466px; }

  .wordmark {
    position: absolute;
    display: flex;
    align-items: center;
    gap: 14px;
  }
  .wordmark__mark {
    width: 34px;
    height: 34px;
    background: var(--brand-orange);
  }
  .wordmark__name {
    color: var(--brand-green);
    font-weight: 700;
    line-height: 1.05;
  }
  .wordmark__name span { display: block; }
  .card--front .wordmark { left: 150px; top: 128px; }
  .card--front .wordmark__name { font-size: 40px; }
  .card--front .wordmark__name .wordmark__sub { font-size: 22px; }

  .card--back .wordmark { left: 56px; top: 140px; }
  .card--back .wordmark__mark { width: 26px; height: 26px; }
  .card--back .wordmark__name { font-size: 30px; }
  .card--back .wordmark__name .wordmark__sub { font-size: 17px; }

  .back-shape {
    position: absolute;
    inset: 0;
    width: 600px;
    height: 340px;
  }
  .contact {
    position: absolute;
    right: 30px;
    top: 26px;
    text-align: right;
    color: var(--ink-white);
    font-size: 14px;
    line-height: 1.35;
  }
  .contact__name { font-weight: 700; font-size: 15px; }
  .contact__role { margin-bottom: 40px; }
  .contact__address { margin-bottom: 26px; }
  .contact__line {
    display: flex;
    justify-content: flex-end;
    align-items: center;
    gap: 6px;
  }
  .contact__line svg { width: 12px; height: 12px; flex: none; }
  .contact__web { margin-top: 2px; }
</style>
</head>
<body>
<main class="canvas">

  <section class="card card--front" aria-label="Card front">
    <div class="wordmark">
      <div class="wordmark__mark"></div>
      <div class="wordmark__name">
        <span>Verdane</span>
        <span class="wordmark__sub">Oil Services</span>
      </div>
    </div>
  </section>

  <section class="card card--back" aria-label="Card back">
    <svg class="back-shape" viewBox="0 0 600 340" aria-hidden="true">
      <path d="M290 0 H600 V340 H330 C405 250 415 95 290 0 Z" fill="var(--brand-orange)"/>
      <path d="M278 0 C400 80 400 250 316 340" fill="none" stroke="var(--ink-white)" stroke-width="5"/>
      <path d="M318 340 C372 276 392 200 372 120 C400 200 392 280 350 340 Z" fill="var(--swoosh-grey)"/>
    </svg>

    <div class="wordmark">
      <div class="wordmark__mark"></div>
      <div class="wordmark__name">
        <span>Verdane</span>
        <span class="wordmark__sub">Oil Services</span>
      </div>
    </div>

    <div class="contact">
      <p class="contact__name">Marlo Quinn-Avery</p>
      <p class="contact__role">Consultant</p>
      <p class="contact__address">41 Harbour Point,<br>Quay Lane</p>
      <p class="contact__line">012 555 0148
        <svg viewBox="0 0 12 12" aria-label="Phone"><path d="M2 1 L4.5 1 L5.5 3.5 L4 4.5 C4.8 6.2 5.8 7.2 7.5 8 L8.5 6.5 L11 7.5 L11 10 C6 10.5 1.5 6 2 1 Z" fill="var(--ink-white)"/></svg>
      </p>
      <p class="contact__line">012 555 0149
        <svg viewBox="0 0 12 12" aria-label="Mobile"><rect x="3" y="0.5" width="6" height="11" rx="1" fill="var(--ink-white)"/><rect x="4" y="2" width="4" height="6.5" fill="var(--brand-orange)"/></svg>
      </p>
      <p class="contact__line">hello@verdaneoil.com
        <svg viewBox="0 0 12 12" aria-label="Email"><rect x="0.5" y="2.5" width="11" height="7" fill="var(--ink-white)"/><path d="M0.8 2.8 L6 6.6 L11.2 2.8" fill="none" stroke="var(--brand-orange)" stroke-width="1"/></svg>
      </p>
      <p class="contact__web">www.verdaneoil.com</p>
    </div>
  </section>

</main>
</body>
</html>
```